Fern Acupuncture Business Card Design

I would like a business card design for my acupuncture business which is based from 2 practices in Melbourne, Australia.

The front of the card should include:

*The Logo
* Name - Miranda Tesselhoff (B.App.Sc.(TCM), Dip.Rem.Mass.). (I would like the letters after my name in slightly smaller font)
* Mobile number - 0472 318 604
* Web address - www.fernacupuncture.com.au

On the back of the card I would somehow like to fit my 2 clinic addresses in. They are:

The Calm & Balance Rooms
842 Pellam St, Camberwell VIC 3124
Ph: 1300 287 419

Riverbend Natural Therapies & Herbal Practice
19 Quillon Ave, Malvern East VIC 3145
Ph: (03) 9731 4052

If there is space, I'd also like to add to the back of the card - Next Appointment............................ (or something along those lines).

Thanks and happy designing!

Target Market(s)

Health consumers, and colleagues in the health industry

Industry/Entity Type

Clinic

Contact Information for Business Card

as above in brief

Requirements
Must have
• I've seen some ok designs coming in, however I'd like to avoid the generic look with the added curved line details etc. I don't particularly need extra patterns added to the card. I'd prefer it to look quite clean and simple, and using more earthy colours (I'm not super keen on the lime green that a lot of designs seem to include. I don't mind the full black or white look, (obviously the back side needs to be a lighter colour to allow me to write appointment details on it). I also quite like the idea of the background looking like brown recycled paper (just an idea - that's not 100% necessary).
Nice to have
• I have an idea that I could have the main flower part of the logo printed as metallic.
Should not have
• Generic patterns and too much added detail.

```html
<!DOCTYPE html>
<html lang="en">
<head>
<meta charset="utf-8">
<title>Fern Acupuncture Business Card</title>
<link rel="stylesheet" href="https://fonts.googleapis.com/css2?family=Cinzel:wght@400;600&family=Arimo:wght@400;700&display=swap">
<style>
  :root {
    --page: #ebe6dc;
    --ink: #0d0e10;
    --gold-dark: #b8953f;
    --gold-mid: #d9bd6a;
    --gold-light: #f4e6b6;
    --lime: #a6d13a;
    --paper: #ffffff;
    --gold-grad: linear-gradient(100deg, var(--gold-dark) 0%, var(--gold-light) 35%, var(--gold-mid) 65%, var(--gold-light) 100%);
  }
  * { box-sizing: border-box; margin: 0; padding: 0; }
  html, body { width: 1200px; height: 800px; overflow: hidden; }
  body { background: var(--page); font-family: "Arimo", Arial, sans-serif; position: relative; }

  .card {
    position: absolute; top: 240px; width: 560px; height: 320px;
    box-shadow: 0 10px 28px rgba(0,0,0,.28); overflow: hidden;
  }
  .card--front { left: 30px; background: var(--ink); }
  .card--back { left: 610px; background: var(--paper); }

  /* front */
  .front__rule { position: absolute; left: 0; right: 0; height: 2px; background: var(--gold-mid); }
  .front__rule--top { top: 104px; }
  .front__rule--bottom { top: 214px; }
  .front__band { position: absolute; left: 0; right: 0; top: 112px; height: 96px; background: var(--gold-grad); }
  .brand {
    position: absolute; left: 0; right: 0; top: 112px; height: 96px;
    display: flex; align-items: center; justify-content: center; gap: 12px;
  }
  .brand__dot { width: 18px; height: 18px; border-radius: 50%; background: var(--ink); }
  .brand__name { font-family: "Cinzel", serif; font-weight: 600; font-size: 24px; color: var(--ink); letter-spacing: 1px; }

  .practitioner { position: absolute; left: 24px; top: 34px; }
  .practitioner__name { font-family: "Cinzel", serif; font-size: 24px; color: #fff; letter-spacing: .5px; }
  .practitioner__quals { font-size: 11px; font-weight: 700; color: var(--lime); margin-top: 4px; }

  .contact { position: absolute; right: 18px; top: 240px; text-align: right; color: var(--gold-light); font-weight: 700; }
  .contact__row { display: flex; align-items: center; justify-content: flex-end; gap: 8px; }
  .contact__phone { font-size: 18px; }
  .contact__web { font-size: 14px; margin-top: 8px; }

  /* back */
  .back__strip { position: absolute; left: 0; right: 0; background: var(--gold-grad); }
  .back__strip--top { top: 0; height: 62px; border-bottom: 2px solid var(--ink); }
  .back__strip--bottom { top: 202px; bottom: 0; border-top: 2px solid var(--ink); }

  .clinic { position: absolute; color: var(--ink); }
  .clinic--camberwell { right: 22px; top: 8px; text-align: right; }
  .clinic--malvern { left: 22px; top: 226px; }
  .clinic__name { font-weight: 700; font-size: 14px; }
  .clinic--malvern .clinic__name { font-size: 17px; }
  .clinic__line { font-size: 11.5px; margin-top: 2px; display: flex; align-items: center; gap: 5px; }
  .clinic--camberwell .clinic__line { justify-content: flex-end; }
  .clinic--malvern .clinic__line { font-size: 13px; }

  .appointment { position: absolute; left: 22px; right: 22px; top: 84px; color: var(--ink); font-size: 15px; }
  .appointment__title { font-size: 17px; margin-bottom: 12px; }
  .appointment__row { display: flex; align-items: baseline; gap: 6px; margin-bottom: 12px; padding-left: 30px; }
  .appointment__dots { flex: 1; border-bottom: 2px dotted var(--ink); height: 1px; }
</style>
</head>
<body>

<section class="card card--front" aria-label="Card front">
  <div class="front__rule front__rule--top"></div>
  <div class="front__band"></div>
  <div class="front__rule front__rule--bottom"></div>

  <div class="brand">
    <span class="brand__dot"></span>
    <span class="brand__name">Fern Acupuncture</span>
  </div>

  <div class="practitioner">
    <div class="practitioner__name">Miranda Tesselhoff</div>
    <div class="practitioner__quals">(B.App.Sc.(TCM), Dip.Rem.Mass.)</div>
  </div>

  <div class="contact">
    <div class="contact__row contact__phone">
      <span>0472 318 604</span>
      <svg width="12" height="18" viewBox="0 0 12 18" aria-hidden="true">
        <rect x="1" y="1" width="10" height="16" rx="2" fill="none" stroke="#a6d13a" stroke-width="1.8"/>
        <circle cx="6" cy="14" r="1" fill="#a6d13a"/>
      </svg>
    </div>
    <div class="contact__row contact__web">
      <span>www.fernacupuncture.com.au</span>
      <svg width="15" height="15" viewBox="0 0 16 16" aria-hidden="true">
        <circle cx="8" cy="8" r="7" fill="none" stroke="#a6d13a" stroke-width="1.6"/>
        <ellipse cx="8" cy="8" rx="3" ry="7" fill="none" stroke="#a6d13a" stroke-width="1.2"/>
        <line x1="1" y1="8" x2="15" y2="8" stroke="#a6d13a" stroke-width="1.2"/>
      </svg>
    </div>
  </div>
</section>

<section class="card card--back" aria-label="Card back">
  <div class="back__strip back__strip--top"></div>
  <div class="back__strip back__strip--bottom"></div>

  <div class="clinic clinic--camberwell">
    <div class="clinic__name">The Calm &amp; Balance Rooms</div>
    <div class="clinic__line">842 Pellam St, Camberwell VIC 3124</div>
    <div class="clinic__line">1300 287 419
      <svg width="10" height="10" viewBox="0 0 10 10" aria-hidden="true"><path d="M2 1 L4 3 L3 4.5 Q4.5 6.5 5.5 7 L7 6 L9 8 L7.5 9.5 Q3 8.5 0.5 2.5 Z" fill="#0d0e10"/></svg>
    </div>
  </div>

  <div class="appointment">
    <div class="appointment__title">Next Appointment</div>
    <div class="appointment__row"><span>Date</span><span class="appointment__dots"></span><span>Time</span><span class="appointment__dots"></span></div>
    <div class="appointment__row"><span>Date</span><span class="appointment__dots"></span><span>Time</span><span class="appointment__dots"></span></div>
  </div>

  <div class="clinic clinic--malvern">
    <div class="clinic__name">Riverbend Natural Therapies &amp; Herbal Practice</div>
    <div class="clinic__line">19 Quillon Ave, Malvern East VIC 3145</div>
    <div class="clinic__line">
      <svg width="11" height="11" viewBox="0 0 10 10" aria-hidden="true"><path d="M2 1 L4 3 L3 4.5 Q4.5 6.5 5.5 7 L7 6 L9 8 L7.5 9.5 Q3 8.5 0.5 2.5 Z" fill="#0d0e10"/></svg>
      (03) 9731 4052
    </div>
  </div>
</section>

</body>
</html>
```